Advanced Therapeutic Massage Therapist

I need a business card advertising my massage services as an advanced therapeutic massage therapist. I offer advanced therapeutic massage, swedish and deep tissue. I want to create a simple, professional and feminine card. I like bright colours and creativity.

I prefer a bold and experimental approach rather than something status-quo. A card to suggest therapeutic healing through dynamic massage. Motifs, shapes or layout which suggest movement and flow.
Updates

Target Market(s)

Everybody!

Industry/Entity Type

Health And Wellness

Contact Information for Business Card

The card should include:
My name, logo, services offered and my contact details.

Sláine Dunleavy
Massage Therapist

- Swedish - Deep Tissue - Advanced Therapeutic

Phone: (+353) 87 216 4093
Email: regenerate@slainedunleavy-example.com
Website: www.slainedunlevy-example.com

Font styles to use
Serif
Sans Serif
Decorative
Script

Colors

Designer to choose colors to be used in the design.

Requirements
Must have
• An example may contain something like this, yet concise:
• "Sláine Dunleavy
• Massage Therapist
• - Swedish - Deep Tissue - Advanced Therapeutic"
Nice to have
• This sentence is optional:
• Imagery such as a logo or symbol. I have attached a file containing a logo I had produced however the name is incorrect now as it is "Sláine" not "Nelly". It could be edited to change it to Sláine.
• I have sent the file as .psd .jpg. .pdf and .png
• I like when the card conveys energy, movement, pressure points, flow etc.
• I just like the designer to follow their own style and ideas. I like bright colours but must have a lot of a base colour to offset it. I really prefer them to follow their own inspiration. That is my preference.
Should not have
• Pine trees, non-native trees to Britain and Ireland, exotic flowers or animals that are not native to Britain and Ireland.
• I don't like brown as the background colour of the card.
• The cars shouldn't look like a wedding invitation i.e too many floral type designs.

```html
<!DOCTYPE html>
<html lang="en">
<head>
<meta charset="utf-8">
<title>Sláine Dunleavy – Massage Therapist Business Card</title>
<link rel="stylesheet" href="https://fonts.googleapis.com/css2?family=Cormorant+Garamond:ital,wght@1,500&family=Raleway:wght@400;500&display=swap">
<style>
  :root {
    --backdrop: #111111;
    --card: #0b0b0b;
    --card-edge: #1c1c1c;
    --gold: #d9a531;
    --gold-light: #f0c45a;
    --gold-deep: #9c6414;
    --ink-light: #e8e8e8;
  }
  * { margin: 0; padding: 0; box-sizing: border-box; }
  html, body {
    width: 1200px;
    height: 1000px;
    overflow: hidden;
    background: var(--backdrop);
  }
  .stage {
    position: relative;
    width: 1200px;
    height: 1000px;
  }
  .card {
    position: absolute;
    width: 520px;
    height: 300px;
    border-radius: 22px;
    background: radial-gradient(circle at 30% 25%, #161616 0%, var(--card) 70%);
    border: 1px solid var(--card-edge);
    box-shadow: 0 18px 40px rgba(0,0,0,0.6);
    overflow: hidden;
  }
  .card--front { left: 60px; top: 300px; }
  .card--back  { left: 620px; top: 400px; }

  .logo-circle {
    position: absolute;
    left: 100px;
    top: 40px;
    width: 120px;
    height: 120px;
    border-radius: 50%;
    border: 3px solid var(--gold);
  }
  .identity {
    position: absolute;
    left: 250px;
    top: 80px;
  }
  .identity__name {
    font-family: "Cormorant Garamond", serif;
    font-style: italic;
    font-weight: 500;
    font-size: 31px;
    color: var(--gold);
    line-height: 1;
  }
  .identity__role {
    font-family: "Raleway", sans-serif;
    font-size: 15px;
    color: var(--ink-light);
    margin-top: 6px;
  }
  .contact {
    list-style: none;
    margin-top: 10px;
    font-family: "Raleway", sans-serif;
    font-size: 14px;
    color: var(--ink-light);
  }
  .contact li {
    display: flex;
    align-items: center;
    gap: 8px;
    margin-top: 4px;
  }
  .contact svg { width: 12px; height: 12px; fill: var(--gold); flex: none; }
  .services {
    position: absolute;
    left: 40px;
    bottom: 42px;
    font-family: "Cormorant Garamond", serif;
    font-style: italic;
    font-weight: 500;
    font-size: 19px;
    color: var(--gold);
    word-spacing: 2px;
  }
  .services .sep { color: #8a6a2a; margin: 0 14px; font-style: normal; }

  .ornament-field {
    position: absolute;
    inset: 0;
    background:
      radial-gradient(ellipse 46% 52% at 58% 40%, rgba(240,196,90,0.55) 0%, rgba(200,140,40,0.35) 45%, rgba(11,11,11,0) 100%),
      radial-gradient(ellipse 28% 40% at 20% 32%, rgba(217,165,49,0.35) 0%, rgba(11,11,11,0) 100%),
      radial-gradient(ellipse 26% 42% at 90% 48%, rgba(217,165,49,0.38) 0%, rgba(11,11,11,0) 100%),
      radial-gradient(ellipse 14% 22% at 2% 40%, rgba(217,165,49,0.25) 0%, rgba(11,11,11,0) 100%);
  }
  .tagline {
    position: absolute;
    left: 22px;
    right: 22px;
    bottom: 30px;
    font-family: "Raleway", sans-serif;
    font-size: 12.5px;
    color: var(--gold);
    white-space: nowrap;
  }
</style>
</head>
<body>
  <main class="stage">
    <section class="card card--front" aria-label="Card front">
      <div class="logo-circle" aria-hidden="true"></div>
      <div class="identity">
        <h1 class="identity__name">Sláine Dunleavy</h1>
        <p class="identity__role">Massage Therapist</p>
        <ul class="contact">
          <li>
            <svg viewBox="0 0 24 24" aria-hidden="true"><path d="M6.6 10.8a15.2 15.2 0 0 0 6.6 6.6l2.2-2.2a1 1 0 0 1 1-.25 11.4 11.4 0 0 0 3.6.57 1 1 0 0 1 1 1V20a1 1 0 0 1-1 1A17 17 0 0 1 3 4a1 1 0 0 1 1-1h3.5a1 1 0 0 1 1 1c0 1.25.2 2.45.57 3.57a1 1 0 0 1-.25 1z"/></svg>
            (+353) 87 216 4093
          </li>
          <li>
            <svg viewBox="0 0 24 24" aria-hidden="true"><path d="M2 5h20v14H2z M2 5l10 8 10-8" /></svg>
            slainemassage@example.com
          </li>
        </ul>
      </div>
      <p class="services">Swedish<span class="sep">|</span>Deep Tissue<span class="sep">|</span>Advanced Therapeutic</p>
    </section>

    <section class="card card--back" aria-label="Card back">
      <div class="ornament-field" role="img" aria-label="Gold foil flowing tree with swirling branches"></div>
      <p class="tagline">NTHB qualified specialising in advanced therapeutic and deep tissue massage</p>
    </section>
  </main>
</body>
</html>
```